Clean & Inspiring Web Design Project

Tallowmere Object Works, LLC (also known as T7-Works) is a company which provides 3D printing services and products. The emphasis is on making these products and services available to the mass-market - customers and users who may or may not have prior experience with 3D printing and/or rapid prototyping technologies. We are a start-up company, looking to build a clean and creativity inspiring brand - our site must encourage visitor to engage and make something. Our aim is to help take mere ideas and turn them into tangible items. We want to show a fusion of ideas (e.g. pencil sketches on graph paper) with design tools (e.g. CAD and drafting software) and rapid prototyping (e.g. Kindlo 3D printers, Stereolithography Machines, etc.). We would like the website to appear professional but at the same time easy to navigate and a good balance between text and pictures. The final design should inspire customers to nurture their ideas into real products and communicate our services to our customers. Our site should have the feel of a vibrant social community with the added benefit of tangible physical creations.

Target Market(s)

People with great ideas that need to be designed into a real product

Industry/Entity Type

Printing

Requirements
Must have
• - Website design should include 2 layouts - one for a "landing page" and one for a "content page"
- Website design must incorporate attached company logo (or derivative of this logo)
- Website design should incorporate the menu options shown in the attached PDF UI concept (UI does not necessarily need to look like the provided concept, just include all the clickable elements)
- Website design must portray an innovative and cooperative design environment with a look-and-feel that appeals to both amateur and professional designers.
- Please include pictures, illustrations and photographs (as needed) related to 3D printing, CAD design, conventional drafting, engineering and manufacturing industries.
- Design should support scaling to multiple screen sizes, from tablet computers (e.g. Zelo) to very large screen PCs.
- Design should include Username & Password fields for login or a button to pull up a login popup.
Nice to have
• - Website design could include "Invent", "Make", "Produce" and "Buy" options that slowly cycle through - with appropriate photos / graphics. These "menu options" would also be mouse-over enabled to switch into the appropriate context as the cursor enters that region (e.g. mouse over the "Invent" text would bring up page 2, etc.). (See attached Original UI Thoughts)
Should not have
• Requirements - Should Not Have:
- Website design should not portray a service that is very expensive or complicated - we are a reasonably priced service meant to be friendly with amateur inventors
- Website design should not be overly complicated - please keep it reasonably simple
- Website design should not be overly trendy
- Website design should not use more than 2 font styles, gaudy fonts, etc.
- Website design should not be "campy" or "tacky" - playful is ok, but please keep it elegant
- Website design should not be overly masculine or feminine - we will have both women and men as customers

```html
<!DOCTYPE html>
<html lang="en">
<head>
<meta charset="utf-8">
<title>Tallowmere Object Works</title>
<link href="https://fonts.googleapis.com/css2?family=Arimo:wght@400;700&family=Roboto+Condensed:wght@400;700&display=swap" rel="stylesheet">
<style>
:root{
  --blue:#2d8fc4;
  --blue-light:#6cc0e4;
  --blue-dark:#3c93bf;
  --ink:#444;
  --ink-soft:#666;
  --grey-text:#8a8a8a;
  --line:#c9c9c9;
  --footer:#d4d4d4;
  --black:#000;
  --white:#fff;
}
*{box-sizing:border-box;margin:0;padding:0}
html,body{width:1200px;height:675px;overflow:hidden;background:var(--white)}
body{position:relative;font-family:"Arimo",Arial,sans-serif;color:var(--ink)}
.wrap{position:absolute;left:171px;width:858px}

.site-header{position:absolute;top:0;left:0;width:1200px;height:73px;background:linear-gradient(#fff,#ececec)}
.brand{position:absolute;left:176px;top:18px;font-family:"Roboto Condensed",sans-serif;font-weight:700;font-size:21px;line-height:22px;color:var(--blue);width:130px}
.login{position:absolute;left:608px;top:10px;width:420px;font-size:9px;color:var(--ink-soft)}
.login h2{font-weight:400;font-size:12.5px;color:var(--blue);letter-spacing:.3px;margin-bottom:5px}
.login-row{display:flex;align-items:center;gap:5px}
.login-row label{margin-left:2px}
.field{width:135px;height:17px;border:1px solid #b9b9b9;border-radius:4px;background:linear-gradient(#fafafa,#fff)}
.submit{margin-left:12px;width:57px;height:16px;border-radius:3px;border:1px solid #3b8fbf;background:linear-gradient(#6cc0e8,#3592c6);color:#fff;font-size:9px;text-align:center;line-height:14px}
.login-links{display:flex;gap:10px;margin:7px 0 0 189px;font-size:8.5px}
.check{display:inline-block;width:8px;height:8px;border:1px solid #aaa;vertical-align:-1px;margin-right:3px;background:#fff}

.main-nav{position:absolute;top:73px;left:0;width:1200px;height:27px;background:linear-gradient(#fdfdfd,#e3e3e3);border-top:1px solid #d7d7d7;border-bottom:1px solid #cfcfcf}
.main-nav ul{list-style:none;display:flex;position:absolute;left:171px;top:0;height:26px}
.main-nav li{font-size:10.5px;color:var(--ink);line-height:26px;text-align:center;border-right:1px solid #d2d2d2}
.main-nav li:last-child{border-right:0}
.main-nav li.is-active{background:linear-gradient(#bdbdbd,#a9a9a9);color:#fff}

.hero{position:absolute;top:100px;left:0;width:1200px;height:310px;background:var(--black)}
.hero-photo{position:absolute;left:150px;top:0;width:900px;height:310px;
  background:radial-gradient(ellipse 60% 75% at 75% 30%,#f4ef70 0%,#e9b54a 35%,#7a5a2a 65%,rgba(0,0,0,0) 100%),
  linear-gradient(90deg,#000 0%,#3a2a12 20%,#3a3018 80%,#000 100%)}
.hero-caption{position:absolute;left:171px;top:182px;width:429px;height:75px;background:var(--black);color:#fff;font-family:"Roboto Condensed",sans-serif;font-weight:700;padding:11px 10px}
.hero-caption h1{font-size:21px;line-height:24px}
.hero-caption p{font-size:10.5px;margin-top:10px}

.services{top:410px;display:flex;gap:2.5px;height:49px}
.service{flex:1;background:linear-gradient(var(--blue-light),var(--blue-dark));border-radius:0 0 3px 3px;color:#fff;padding:9px 0 0 23px}
.service h3{font-family:"Roboto Condensed",sans-serif;font-weight:700;font-size:13px;line-height:14px}
.service p{font-size:8.5px;margin-top:4px}

.welcome{top:476px;width:628px}
.welcome h2{font-family:"Roboto Condensed",sans-serif;font-weight:700;line-height:1}
.welcome .lead{font-size:18px;color:var(--grey-text)}
.welcome .name{font-size:24px;color:var(--blue);margin-top:2px}
.welcome p{font-size:8.4px;line-height:15.5px;text-align:justify;color:var(--ink);margin-top:10px}
.welcome p+p{margin-top:14px}

.contact-card{position:absolute;left:819px;top:476px;width:209px;height:128px;border:1px solid #ccc;border-radius:3px;overflow:hidden;background:linear-gradient(135deg,#e9e9e9,#9a9a9a 55%,#2b2b2b)}
.contact-card .bar{position:absolute;left:0;bottom:0;width:100%;height:41px;background:rgba(0,0,0,.75);color:#fff;font-family:"Roboto Condensed",sans-serif;font-weight:700;font-size:15.5px;line-height:41px;padding-left:10px}

.site-footer{position:absolute;top:639px;left:0;width:1200px;height:36px;background:var(--footer);font-size:8.8px;color:var(--ink)}
.site-footer ul{list-style:none;display:flex;position:absolute;left:179px;top:13px}
.site-footer li+li::before{content:"|";margin:0 10px}
.copyright{position:absolute;left:822px;top:13px}
.copyright span{color:var(--blue)}
</style>
</head>
<body>
<header class="site-header">
  <div class="brand">Tallowmere Object Works</div>
  <form class="login">
    <h2>USER LOGIN :</h2>
    <div class="login-row">
      <label>Name :</label><span class="field"></span>
      <label>Login :</label><span class="field"></span>
      <span class="submit">Submit</span>
    </div>
    <div class="login-links"><span>Forget your password ?</span><span><i class="check"></i>Register now</span></div>
  </form>
</header>

<nav class="main-nav">
  <ul>
    <li class="is-active" style="width:85px">Home</li>
    <li style="width:91px">About Us</li>
    <li style="width:100px">CAD design</li>
    <li style="width:145px">Conventional drafting</li>
    <li style="width:107px">Engineering</li>
    <li style="width:161px">Manufacturing industries</li>
    <li style="width:96px">Contact Us</li>
  </ul>
</nav>

<section class="hero">
  <div class="hero-photo" role="img" aria-label="Silhouette of an industrial plant with towers and pipes against a glowing orange and yellow sky"></div>
</section>
<div class="hero-caption">
  <h1>We are 3D printing services company and</h1>
  <p>We do CAD design, Conventional drafting, Engineering and Manufacturing industries</p>
</div>

<section class="wrap services">
  <div class="service"><h3>CAD DESIGN</h3><p>Lorem Ipsum is simply dummy text.</p></div>
  <div class="service"><h3>CONVENTIONAL DRAFTING</h3><p>Lorem Ipsum is simply dummy text.</p></div>
  <div class="service"><h3>ENGINEERING</h3><p>Lorem Ipsum is simply dummy text.</p></div>
  <div class="service"><h3>MANUFACTURING INDUSTRIES</h3><p>Lorem Ipsum is simply dummy text.</p></div>
</section>

<section class="wrap welcome">
  <h2 class="lead">Welcome to</h2>
  <h2 class="name">Tallowmere Object Works</h2>
  <p>Lorem Ipsum is simply dummy text of the printing and typesetting industry. Lorem Ipsum has been the industry's standard dummy text ever since the 1500s, when an unknown printer took a galley of type and scrambled it to make a type specimen book. It has survived not only five centuries, but also the leap into electronic typesetting, remaining essentially unchanged. It was popularised in the 1960s.</p>
  <p>Lorem Ipsum is simply dummy text of the printing and typesetting industry. Lorem Ipsum has been the industry's standard dummy text ever since the 1500s, when an unknown printer took a galley of type and scrambled it to make a type specimen book.</p>
</section>

<aside class="contact-card" role="img" aria-label="Business team in suits reviewing documents around a table">
  <div class="bar">Call Us : +00 0000 000 000</div>
</aside>

<footer class="site-footer">
  <ul>
    <li>Home</li><li>About Us</li><li>CAD design</li><li>Conventional drafting</li><li>Engineering</li><li>Manufacturing industries</li><li>Contact Us</li>
  </ul>
  <div class="copyright">© 2012 <span>Tallowmere Object Works</span>. All rights reserved</div>
</footer>
</body>
</html>
```